Building company buisness cards

We are looking for a sharp modern new look for our business cards.
We are a New Zealand based company that specialises in house and land packages.
We have attached a photo of the current logo and would like to see if it can be improved somehow if needed.
We are open to any colours but we have chosen green at this stage.
Feel free to change the font and make the logo smarter looking.
Play with the colours and see what looks best.

We want a card that looks so good know one will want to throw it away!

Target Market(s)

Home buyers

Industry/Entity Type

Building

Contact Information for Business Card

Derek Tolvane
0217394062
dtolvane@quillmarkhomesteads.co.nz
quillmarkhomesteads.co.nz

Font styles to use
Serif
Sans Serif

Colors

Designer to choose colors to be used in the design.

Requirements
Must have
• Logo and company name on one side, details on the other side
Nice to have
• Color codes for the original green are HEX #4a8028, RGB(74,128,40), CMYK(42,0,69,50)
• Round corners, Raised and/or spot UV

```html
<!DOCTYPE html>
<html lang="en">
<head>
<meta charset="utf-8">
<title>Quillmark Homesteads – Business Cards</title>
<link href="https://fonts.googleapis.com/css2?family=Arimo:wght@700&family=Lato:wght@400;900&display=swap" rel="stylesheet">
<style>
  :root{
    --bg:#c8c9cb;
    --paper:#ffffff;
    --green:#4a8628;
    --band:#6b6b6b;
    --ink:#444444;
    --shadow:rgba(0,0,0,.28);
  }
  *{margin:0;padding:0;box-sizing:border-box}
  html,body{width:1200px;height:940px;overflow:hidden;background:var(--bg)}
  body{position:relative;font-family:'Lato',sans-serif}

  .card{position:absolute;width:636px;height:363px;background:var(--paper);
        border-radius:27px;overflow:hidden;box-shadow:0 4px 10px var(--shadow)}
  .card--front{left:135px;top:69px}
  .card--back{left:473px;top:498px}

  /* front */
  .brand{position:absolute;display:flex;align-items:center;gap:12px;
         font-family:'Lato',sans-serif;font-weight:900;color:var(--green)}
  .brand__dot{width:30px;height:30px;border-radius:50%;background:var(--green)}
  .card--front .brand{left:126px;top:68px;font-size:40px;letter-spacing:-.5px}

  .band-top{position:absolute;left:0;top:186px;width:100%;height:37px;background:var(--band)}
  .band-name{position:absolute;left:0;top:186px;width:324px;height:77px;background:var(--band)}
  .green-field{position:absolute;left:0;top:223px;width:100%;bottom:0;background:var(--green)}
  .band-rule{position:absolute;left:0;top:262px;width:330px;height:2px;background:var(--paper)}
  .holder-name{position:absolute;left:35px;top:202px;font-family:'Arimo',sans-serif;
               font-weight:700;font-size:33px;color:var(--paper);line-height:40px;white-space:nowrap}
  .portrait{position:absolute;left:280px;top:176px;width:88px;height:88px;border-radius:50%;
            background:var(--band);border:2px solid var(--paper);box-shadow:0 0 0 2px var(--band)}

  .address{position:absolute;left:48px;top:290px;color:var(--paper);font-size:15.5px;line-height:23px}
  .contacts{position:absolute;left:349px;top:269px;width:272px;list-style:none;color:var(--paper);
            font-size:14.5px;letter-spacing:-.15px}
  .contacts li,.address{display:flex;gap:7px;align-items:flex-start;white-space:nowrap}
  .contacts li{height:27px;align-items:center}
  .icon{width:14px;height:14px;flex:none;fill:none;stroke:var(--paper);stroke-width:1.6}
  .address .icon{margin:4px 0 0 -12px}

  /* back */
  .card--back .brand{left:0;right:0;top:92px;flex-direction:column;gap:4px;
                     font-size:40px;line-height:40px;text-align:center}
  .card--back .brand__dot{width:44px;height:44px;margin-bottom:14px}
  .back-rule{position:absolute;left:236px;top:265px;width:141px;height:2px;background:var(--green)}
  .back-url{position:absolute;left:0;right:0;top:319px;text-align:center;font-size:16px;
            letter-spacing:2.4px;color:var(--ink)}
  .back-url .accent{color:var(--green)}
</style>
</head>
<body>

<section class="card card--front">
  <div class="brand"><span class="brand__dot"></span><span class="brand__name">Quillmark Homesteads</span></div>
  <div class="green-field"></div>
  <div class="band-top"></div>
  <div class="band-name"></div>
  <div class="band-rule"></div>
  <div class="holder-name">Derek Tolvane</div>
  <div class="portrait" role="img" aria-label="Portrait photo of Derek Tolvane"></div>

  <div class="address">
    <svg class="icon" viewBox="0 0 16 16"><circle cx="8" cy="8" r="7"/><circle cx="8" cy="7" r="2.2"/><path d="M8 13 5 8.5M8 13l3-4.5"/></svg>
    <span>123, Street Name, City Name<br>Zipcode - 01234</span>
  </div>

  <ul class="contacts">
    <li><svg class="icon" viewBox="0 0 16 16"><circle cx="8" cy="8" r="7"/><path d="M6 4.5c-1 1-.8 3.5 1 5.5s4 2.6 5 1.5l-1.5-1.5-1 .7-2.5-2.5.7-1z"/></svg>0217394062</li>
    <li><svg class="icon" viewBox="0 0 16 16"><path d="M1.5 6.5 8 2l6.5 4.5V14h-13z"/><path d="M1.5 6.5 8 10.5l6.5-4"/></svg>dtolvane@quillmarkhomesteads.co.nz</li>
    <li><svg class="icon" viewBox="0 0 16 16"><circle cx="8" cy="8" r="7"/><ellipse cx="8" cy="8" rx="3" ry="7"/><path d="M1 8h14M2.5 4.5h11M2.5 11.5h11"/></svg>www.quillmarkhomesteads.co.nz</li>
  </ul>
</section>

<section class="card card--back">
  <div class="brand"><span class="brand__dot"></span><span>Quillmark</span><span>Homesteads</span></div>
  <div class="back-rule"></div>
  <p class="back-url">www.<span class="accent">quillmarkhomesteads</span>.co.nz</p>
</section>

</body>
</html>
```